Payment company requires web design

We need a web design for a new company based in Singapore.

The company focuses on providing 2 key products: 1) an alternative payment option (i.e. like quib or trelloquin options) on the traditional checkout process 2) a replacement/outsource of a merchants payment page. Key in the UX flow is a end customer dashboard that manages all payments.

We look to provide a simple, fluid and easy to use payment process. The dashboard is minimalistic that allows easy navigation, review of transactions and all available options through gamification.

The final design should communicate ease of use, flexibility and transparency.

Target Market(s)

The value is for the merchant - retail/travel/insurance companies. However its the merchant's end customers that are the target and who the UX is built for.

Industry/Entity Type

It Company

Logo Text

zelnar

Number of Pages Required

5+ page

Colors
ec1f27

Requirements
Must have
• 7 pages mimicking UX flow
• payment page * 2 - 1) alternative payment type 2) outsource of merchants payment page to our business
• our landing page
• end customer verification page
• end customer registration
• customer dashboard
• UX flow in attached file
Nice to have
• open to ideas
• have asked for the logo to be added
• logo to have the colour red (chinese for prosperity)
• the company is all about flexibility, transparency in personal finance management with the option of instalment payments

```html
<!DOCTYPE html>
<html lang="en">
<head>
<meta charset="utf-8">
<title>Zelnar — Payment Processing</title>
<link href="https://fonts.googleapis.com/css2?family=Lato:wght@300;400;700&display=swap" rel="stylesheet">
<style>
  :root {
    --brand-red: #b3373a;
    --text-dark: #444444;
    --text-body: #8a8a8a;
    --text-muted: #c4c4c4;
    --line: #ececec;
    --footer-bg: #f7f7f7;
    --white: #ffffff;
  }
  * { box-sizing: border-box; margin: 0; padding: 0; }
  html, body { width: 1200px; height: 2214px; overflow: hidden; }
  body {
    position: relative;
    background: var(--white);
    font-family: "Lato", Arial, sans-serif;
    color: var(--text-dark);
  }
  .abs { position: absolute; }

  /* Header */
  .site-header { position: absolute; left: 0; top: 0; width: 1200px; height: 111px; background: var(--white); }
  .brand { font-family: "Lato", Arial, sans-serif; font-weight: 700; color: var(--brand-red); font-size: 29px; letter-spacing: 2px; text-transform: uppercase; }
  .site-header .brand { left: 190px; top: 40px; }
  .search { left: 444px; top: 41px; width: 263px; height: 34px; border: 1px solid #d8d8d8; border-radius: 17px; }
  .search span { position: absolute; left: 15px; top: 10px; font-size: 11px; color: #999; letter-spacing: .5px; }
  .search svg { position: absolute; right: 11px; top: 10px; }
  .main-nav a { position: absolute; top: 52px; font-size: 11px; color: var(--text-dark); text-decoration: none; letter-spacing: .3px; }

  /* Hero */
  .hero { left: 0; top: 111px; width: 1200px; height: 549px;
    background: radial-gradient(ellipse at 62% 35%, #cdb9ac 0%, #b9c6c4 30%, #a9aeb0 60%, #8f9497 100%); }
  .hero-title { left: 0; width: 1200px; top: 430px; text-align: center; color: var(--white); font-size: 25px; font-weight: 300; letter-spacing: .5px; }
  .btn { position: absolute; display: flex; align-items: center; justify-content: center; font-size: 13px; letter-spacing: .5px; border-radius: 24px; text-transform: uppercase; }
  .btn-outline-light { left: 444px; top: 487px; width: 151px; height: 46px; border: 2px solid var(--white); color: var(--white); }
  .btn-solid { background: var(--brand-red); color: var(--white); }
  .hero .btn-solid { }
  .dot { position: absolute; top: 606px; width: 8px; height: 8px; border-radius: 50%; background: var(--white); }
  .dot.active { background: var(--brand-red); }

  /* About */
  .section-title { left: 0; width: 1200px; text-align: center; font-size: 22px; font-weight: 400; letter-spacing: .5px; text-transform: uppercase; }
  .about-title { top: 748px; color: var(--brand-red); }
  .lead { left: 204px; width: 792px; text-align: center; font-size: 13px; line-height: 23px; color: var(--text-body); }
  .feature { position: absolute; top: 895px; width: 240px; text-align: center; }
  .feature svg { display: block; margin: 0 auto; }
  .feature p { margin-top: 22px; font-size: 13px; color: var(--text-dark); letter-spacing: .4px; }
  .divider { position: absolute; height: 1px; background: var(--line); }

  /* Audience cards */
  .card { position: absolute; top: 1108px; width: 388px; height: 271px; border-radius: 35px; padding: 48px 26px 0 27px; }
  .card-merchant { left: 202px; background: var(--brand-red); color: var(--white); }
  .card-consumer { left: 611px; border: 1px solid #e4e4e4; background: var(--white); }
  .card h3 { display: flex; align-items: center; gap: 14px; font-size: 22px; font-weight: 400; letter-spacing: .3px; text-transform: uppercase; }
  .card-consumer h3 { color: #777; }
  .card p { margin-top: 26px; font-size: 17px; line-height: 27px; font-weight: 400; }
  .card-consumer p { color: var(--text-muted); }
  .card .btn { left: 24px; top: 204px; width: 148px; height: 43px; font-size: 12px; }
  .btn-white { background: var(--white); color: var(--brand-red); }

  /* Testimonials */
  .work-title { top: 1504px; color: #555; }
  .client-name { left: 0; width: 1200px; top: 1618px; display: flex; justify-content: center; align-items: center; gap: 10px; }
  .client-name .mark { width: 14px; height: 14px; background: var(--text-dark); }
  .client-name span { font-size: 30px; font-weight: 700; color: var(--text-dark); letter-spacing: .5px; }
  .stars { left: 0; width: 1200px; top: 1693px; display: flex; justify-content: center; gap: 11px; }
  .avatar { left: 564px; top: 1833px; width: 72px; height: 72px; border-radius: 50%; border: 2px solid #eee;
    background: radial-gradient(circle at 50% 40%, #d7b49d 0%, #a98f7d 45%, #e9e9ee 75%); }
  .person { left: 0; width: 1200px; top: 1913px; text-align: center; font-size: 15px; color: #666; }

  /* Footer */
  .site-footer { left: 0; top: 1967px; width: 1200px; height: 195px; background: var(--footer-bg); }
  .site-footer .brand { left: 190px; top: 2036px; }
  .footer-link { position: absolute; font-size: 10.5px; color: #555; letter-spacing: .3px; text-transform: uppercase; }
  .social { position: absolute; top: 2040px; width: 13px; height: 13px; border-radius: 50%; background: #555; }
  .social.first { background: var(--brand-red); }
  .bottom-bar { left: 0; top: 2162px; width: 1200px; height: 52px; background: var(--footer-bg); border-top: 1px solid var(--line); }
  .copyright { left: 0; width: 1200px; top: 2181px; text-align: center; font-size: 10.5px; color: #555; letter-spacing: .3px; }
</style>
</head>
<body>

<header class="site-header">
  <div class="brand abs">zelnar</div>
  <div class="search abs">
    <span>SEARCH</span>
    <svg width="12" height="12" viewBox="0 0 12 12"><circle cx="5" cy="5" r="3.6" fill="none" stroke="#b3373a" stroke-width="1.8"/><line x1="7.7" y1="7.7" x2="11" y2="11" stroke="#b3373a" stroke-width="2"/></svg>
  </div>
  <nav class="main-nav">
    <a style="left:751px">ABOUT</a>
    <a style="left:824px">SUPPORT</a>
    <a style="left:908px">CONTACT US</a>
  </nav>
</header>

<section class="hero abs" role="img" aria-label="Smiling woman working at a laptop in a bright office with colleagues blurred behind">
</section>
<h1 class="hero-title abs">WE ARE PAYMENT PROCESSING COMPANY FROM SINGAPORE</h1>
<div class="btn btn-outline-light">Login</div>
<div class="btn btn-solid" style="left:607px;top:488px;width:147px;height:44px">Register</div>
<span class="dot active" style="left:567px"></span>
<span class="dot" style="left:586px"></span>
<span class="dot" style="left:605px"></span>
<span class="dot" style="left:623px"></span>

<section class="about">
  <h2 class="section-title about-title abs">About zelnar</h2>
  <p class="lead abs" style="top:800px">Sed ut perspiciatis unde omnis iste natus error sit voluptatem accusantium doloremque laudantium, totam rem aperiam, eaque ipsa quae ab illo inventore veritatis et quasi architecto beatae vitae dicta sunt explicabo. Nemo enim ipsam voluptatem</p>

  <div class="feature" style="left:206px">
    <svg width="38" height="32" viewBox="0 0 38 32" fill="none" stroke="#b3373a" stroke-width="4.5">
      <path d="M2 8h7c8 0 12 16 20 16h3"/><path d="M2 24h7c3 0 5-2 7-5"/><path d="M22 12c2-3 4-4 7-4h3"/>
      <path d="M29 2l6 6-6 6" fill="#b3373a" stroke-width="2"/><path d="M29 18l6 6-6 6" fill="#b3373a" stroke-width="2"/>
    </svg>
    <p>FLEXIBILITY</p>
  </div>
  <div class="feature" style="left:479px">
    <svg width="38" height="34" viewBox="0 0 38 34"><path d="M36 1L1 16l10 4 2 12 6-8 9 6z" fill="#b3373a"/><path d="M11 20L36 1 15 23" fill="#8a2729"/></svg>
    <p>TRANSPERENCY</p>
  </div>
  <div class="feature" style="left:748px">
    <svg width="38" height="32" viewBox="0 0 38 32"><rect x="13" y="1" width="12" height="7" rx="2" fill="none" stroke="#b3373a" stroke-width="3"/><rect x="1" y="7" width="36" height="24" rx="3" fill="#b3373a"/><rect x="1" y="16" width="36" height="2" fill="#fff"/><rect x="16" y="14" width="6" height="6" fill="#fff"/></svg>
    <p>INSTALMENT PAYMENT</p>
  </div>
</section>

<div class="divider" style="left:204px;top:1057px;width:792px"></div>

<section class="audiences">
  <article class="card card-merchant">
    <h3>
      <svg width="26" height="22" viewBox="0 0 26 22"><path d="M2 2h20l-3 18H5z" fill="#fff"/><rect x="0" y="0" width="10" height="10" fill="#fff"/><rect x="3" y="3" width="5" height="5" fill="#b3373a"/></svg>
      Merchant
    </h3>
    <p>Sed ut perspiciatis unde omnis iste natus error sit voluptatem accusantium doloremque.</p>
    <div class="btn btn-white">Read more</div>
  </article>
  <article class="card card-consumer">
    <h3>
      <svg width="22" height="24" viewBox="0 0 22 24"><circle cx="11" cy="6" r="5.5" fill="#b3373a"/><path d="M0 24c0-8 4-11 11-11s11 3 11 11z" fill="#b3373a"/></svg>
      Consumer or personal
    </h3>
    <p>Sed ut perspiciatis unde omnis iste natus error sit voluptatem accusantium doloremque.</p>
    <div class="btn btn-solid">Read more</div>
  </article>
</section>

<div class="divider" style="left:204px;top:1436px;width:792px"></div>

<section class="testimonials">
  <h2 class="section-title work-title abs">Who we work</h2>
  <div class="divider" style="left:453px;top:1554px;width:292px"></div>

  <div class="client-name abs"><i class="mark"></i><span>Lensory</span></div>

  <div class="stars abs">
    <svg width="20" height="19" viewBox="0 0 20 19"><path d="M10 0l3 6.5 7 .8-5.2 4.8 1.4 6.9L10 15.5 3.8 19l1.4-6.9L0 7.3l7-.8z" fill="#b3373a"/></svg>
    <svg width="20" height="19" viewBox="0 0 20 19"><path d="M10 0l3 6.5 7 .8-5.2 4.8 1.4 6.9L10 15.5 3.8 19l1.4-6.9L0 7.3l7-.8z" fill="#b3373a"/></svg>
    <svg width="20" height="19" viewBox="0 0 20 19"><path d="M10 0l3 6.5 7 .8-5.2 4.8 1.4 6.9L10 15.5 3.8 19l1.4-6.9L0 7.3l7-.8z" fill="#b3373a"/></svg>
    <svg width="20" height="19" viewBox="0 0 20 19"><path d="M10 0l3 6.5 7 .8-5.2 4.8 1.4 6.9L10 15.5 3.8 19l1.4-6.9L0 7.3l7-.8z" fill="#b3373a"/></svg>
    <svg width="20" height="19" viewBox="0 0 20 19"><path d="M10 1.5l2.6 5.6 6.1.7-4.5 4.2 1.2 6L10 15 4.6 18l1.2-6L1.3 7.8l6.1-.7z" fill="none" stroke="#b3373a" stroke-width="1.8"/><path d="M10 0v15.5L3.8 19l1.4-6.9L0 7.3l7-.8z" fill="#b3373a"/></svg>
  </div>

  <p class="lead abs" style="top:1745px">Sed ut perspiciatis unde omnis iste natus error sit voluptatem accusantium doloremque laudantium, totam rem aperiam, eaque ipsa quae ab illo inventore veritatis et quasi architecto beatae vitae dicta sunt explicabo. Nemo enim ipsam voluptatem</p>

  <svg class="abs" style="left:75px;top:1756px" width="12" height="18" viewBox="0 0 12 18"><path d="M10 1L2 9l8 8" fill="none" stroke="#bbb" stroke-width="2.5"/></svg>
  <svg class="abs" style="left:1113px;top:1756px" width="12" height="18" viewBox="0 0 12 18"><path d="M2 1l8 8-8 8" fill="none" stroke="#bbb" stroke-width="2.5"/></svg>

  <div class="divider" style="left:453px;top:1818px;width:292px"></div>
  <div class="avatar abs" role="img" aria-label="Portrait photo of Daniel Arun"></div>
  <p class="person abs">Daniel Arun</p>
</section>

<footer class="site-footer abs">
</footer>
<div class="brand abs" style="left:190px;top:2036px">zelnar</div>
<span class="footer-link" style="left:396px;top:2037px">About</span>
<span class="footer-link" style="left:396px;top:2059px">Support</span>
<span class="footer-link" style="left:396px;top:2082px">Contact us</span>
<span class="footer-link" style="left:531px;top:2037px">Leadership team</span>
<span class="footer-link" style="left:531px;top:2059px">Jobs</span>
<span class="footer-link" style="left:700px;top:2037px">Terms of use</span>
<span class="footer-link" style="left:700px;top:2059px">Privacy policy</span>
<span class="social first" style="left:871px" aria-label="Social link"></span>
<span class="social" style="left:893px" aria-label="Social link"></span>
<span class="social" style="left:918px" aria-label="Social link"></span>
<span class="social" style="left:942px" aria-label="Social link"></span>
<div class="bottom-bar abs"></div>
<p class="copyright abs">© 2016 COMPANY NAME &nbsp;|&nbsp; ALL RIGHTS RESERVED</p>

</body>
</html>
```